Dynamic Business Card for Sports Supplements Company

Hi! I'm looking for an awesome business card to match my existing sports supplement company. I have uploaded my current company logo and screenshot of the front page of my website.

I would like to have something dynamic and interesting and utilize the colors in the website - the reds and purples

The business card should be double sided and focus on a unique eye-catching design on the back and include all the relevant company info.

Most importantly, it should say somewhere: "Sign up on our website for a coupon code."

Target Market(s)

Mostly for women gym goers but it shouldn't be too feminine. It should be in keeping with the website design. It should flow and clearly be connected to it

Industry/Entity Type

Business

Contact Information for Business Card

Lorraine K. Vestal
CEO
LVestal@Quorvanexco.com
www.quorvanexco.com
555.417.3820
P.O. Box 47315
Alder Falls, Ohio 00000

Sign up on our website for a coupon code

Font styles to use
Serif
Sans Serif
Other font styles liked:
• Novecento font family and "Quorvanex" is in AR Destine font

Requirements
Must have
• One side should be a bold Quorvanex logo design. Even just the symbol itself may be o.k. (see attached file)

```html
<!DOCTYPE html>
<html lang="en">
<head>
<meta charset="utf-8">
<title>Quorvanex Business Card</title>
<link href="https://fonts.googleapis.com/css2?family=Michroma&family=Open+Sans:wght@400;600&display=swap" rel="stylesheet">
<style>
  :root {
    --brand-red: #e41e26;
    --brand-black: #1c1c1c;
    --card-dark: #232323;
    --card-stripe: #2c2c2c;
    --paper: #ffffff;
    --ink: #222222;
    --muted: #bdbdbd;
    --backdrop: #e6e4e1;
  }
  * { box-sizing: border-box; margin: 0; padding: 0; }
  html, body { width: 1200px; height: 1200px; overflow: hidden; }
  body {
    background: var(--backdrop);
    font-family: "Open Sans", Arial, sans-serif;
    position: relative;
  }
  .card {
    position: absolute;
    left: 150px;
    width: 900px;
    height: 514px;
    overflow: hidden;
    box-shadow: 0 6px 18px rgba(0,0,0,0.18);
  }

  /* Back side */
  .card-back {
    top: 56px;
    background: repeating-linear-gradient(
      to bottom,
      var(--card-dark) 0px,
      var(--card-dark) 4px,
      var(--card-stripe) 4px,
      var(--card-stripe) 6px
    );
    display: flex;
    flex-direction: column;
    align-items: center;
    justify-content: center;
    text-align: center;
  }
  .brand-mark {
    width: 70px;
    height: 70px;
    border-radius: 50%;
    background: var(--brand-red);
    margin-bottom: 26px;
  }
  .brand-wordmark {
    font-family: "Michroma", "Arial Black", sans-serif;
    color: var(--paper);
    font-size: 52px;
    letter-spacing: 3px;
    line-height: 1;
  }
  .brand-tagline {
    font-family: "Michroma", Arial, sans-serif;
    color: var(--muted);
    font-size: 14px;
    letter-spacing: 5px;
    margin-top: 10px;
    text-transform: uppercase;
  }
  .coupon-line {
    color: var(--paper);
    font-size: 22px;
    margin-top: 40px;
  }
  .coupon-line .highlight { color: var(--brand-red); font-weight: 600; }

  /* Front side */
  .card-front {
    top: 630px;
    background: var(--paper);
  }
  .accent-red {
    position: absolute; left: 0; top: 0;
    width: 240px; height: 160px;
    background: var(--brand-red);
  }
  .accent-black {
    position: absolute; left: 0; top: 160px;
    width: 140px; height: 354px;
    background: var(--brand-black);
  }
  .logo-badge {
    position: absolute;
    left: 40px; top: 72px;
    width: 260px; height: 260px;
    border-radius: 50%;
    background: var(--paper);
    border: 12px solid var(--brand-red);
    display: flex;
    align-items: center;
    justify-content: center;
  }
  .logo-badge .badge-name {
    font-family: "Michroma", Arial, sans-serif;
    font-size: 21px;
    color: var(--brand-black);
    letter-spacing: 1px;
  }
  .contact-block {
    position: absolute;
    left: 380px; top: 110px;
    color: var(--ink);
  }
  .person-name {
    font-family: "Michroma", Arial, sans-serif;
    font-weight: 400;
    color: var(--brand-red);
    font-size: 27px;
    letter-spacing: 4px;
    text-transform: uppercase;
    line-height: 1.1;
  }
  .person-title {
    font-size: 21px;
    margin-top: 4px;
    margin-bottom: 28px;
  }
  .contact-list { list-style: none; }
  .contact-list li {
    display: flex;
    align-items: center;
    gap: 12px;
    font-size: 21px;
    line-height: 36px;
  }
  .contact-list svg { width: 18px; height: 18px; flex: none; fill: var(--brand-red); }
  .mailing-address {
    font-size: 21px;
    line-height: 30px;
    margin-top: 26px;
  }
</style>
</head>
<body>

  <section class="card card-back">
    <div class="brand-mark"></div>
    <div class="brand-wordmark">QUORVANEX</div>
    <div class="brand-tagline">Strength In Every Rep</div>
    <p class="coupon-line"><span class="highlight">Sign up</span> on our website for a coupon code</p>
  </section>

  <section class="card card-front">
    <div class="accent-red"></div>
    <div class="accent-black"></div>
    <div class="logo-badge"><span class="badge-name">QUORVANEX</span></div>

    <div class="contact-block">
      <h1 class="person-name">Lorraine K. Vestal</h1>
      <p class="person-title">CEO</p>
      <ul class="contact-list">
        <li>
          <svg viewBox="0 0 24 24" aria-hidden="true"><path d="M6.6 10.8a15.1 15.1 0 0 0 6.6 6.6l2.2-2.2c.3-.3.7-.4 1-.2 1.1.4 2.3.6 3.6.6.6 0 1 .4 1 1V20c0 .6-.4 1-1 1A17 17 0 0 1 3 4c0-.6.4-1 1-1h3.5c.6 0 1 .4 1 1 0 1.3.2 2.5.6 3.6.1.3 0 .7-.2 1z"/></svg>
          555.417.3820
        </li>
        <li>
          <svg viewBox="0 0 24 24" aria-hidden="true"><path d="M2 5h20v14H2zm2 2v.5l8 5 8-5V7zm0 2.9V17h16V9.9l-8 5z"/></svg>
          LVestal@Quorvanexco.com
        </li>
        <li>
          <svg viewBox="0 0 24 24" aria-hidden="true"><path d="M12 2a10 10 0 1 0 0 20 10 10 0 0 0 0-20zm6.9 9h-3a15.6 15.6 0 0 0-1.3-6A8 8 0 0 1 18.9 11zM12 4c.9 1.2 1.7 3.6 1.9 7h-3.8c.2-3.4 1-5.8 1.9-7zM9.4 5a15.6 15.6 0 0 0-1.3 6h-3A8 8 0 0 1 9.4 5zM5.1 13h3a15.6 15.6 0 0 0 1.3 6A8 8 0 0 1 5.1 13zM12 20c-.9-1.2-1.7-3.6-1.9-7h3.8c-.2 3.4-1 5.8-1.9 7zm2.6-1a15.6 15.6 0 0 0 1.3-6h3a8 8 0 0 1-4.3 6z"/></svg>
          www.quorvanexco.com
        </li>
      </ul>
      <p class="mailing-address">P.O. Box 47315<br>Alder Falls, Ohio 00000</p>
    </div>
  </section>

</body>
</html>
```